Awesome business card design needed

We need a new business card design to go with our new logo.
We are a web development agency that specialises in highly complex back-end integrations as opposed to design, our customers are retailers, hotels, hospitals and any other organisation that has a large online marketing department.
Take a look at our website - www.brenoloft.com for some inspiration.
We want our new business cards to exude class, professionalism and style.
We are likely to choose a high-end card to print them on but we want the design of the card itself to really turn heads.
We have no specific colour requirements, the logo as you will see is a turquoise colour R89 G171 B167 #59aba7 but it can also be in white if you want to make the colour of the card something different.
The information on the card should be:
Name
Position
Tel
email
Potentially a double sided card could have our web address, twitter and FB links.

```html
<!DOCTYPE html>
<html lang="en">
<head>
<meta charset="utf-8">
<title>Brenoloft Business Card</title>
<link rel="stylesheet" href="https://fonts.googleapis.com/css2?family=Play:wght@400;700&display=swap">
<style>
  :root {
    --teal: #59aba7;
    --white: #ffffff;
    --ink: #2e3236;
    --rule: #3a3d40;
    --backdrop: #e9ebea;
  }
  * { box-sizing: border-box; margin: 0; padding: 0; }
  html, body {
    width: 1200px; height: 720px; overflow: hidden;
    background: var(--backdrop);
    font-family: "Play", Arial, sans-serif;
  }
  .stage {
    position: relative; width: 1200px; height: 720px;
    display: flex; align-items: center; justify-content: center; gap: 40px;
  }
  .card {
    position: relative; width: 540px; height: 309px;
    box-shadow: 0 6px 18px rgba(0,0,0,0.15);
    overflow: hidden;
  }

  /* Front */
  .card-front { background: var(--white); }
  .front-band {
    position: absolute; left: 0; top: 0; bottom: 0; width: 78px;
    background: var(--teal);
    border-right: 5px solid var(--rule);
  }
  .front-wordmark {
    position: absolute; left: 100px; top: 28px;
    font-weight: 700; font-size: 72px; line-height: 1; letter-spacing: 1px;
    color: var(--teal);
  }
  .holder {
    position: absolute; right: 28px; top: 138px; text-align: right;
  }
  .holder-name { font-weight: 700; font-size: 19px; color: var(--ink); }
  .holder-role { font-size: 14px; color: var(--teal); margin-top: 2px; }
  .contacts {
    position: absolute; left: 100px; top: 186px;
    font-size: 14px; color: var(--ink); list-style: none;
  }
  .contacts li { display: flex; align-items: center; gap: 8px; height: 21px; }
  .contacts svg { width: 13px; height: 13px; flex: none; }
  .address { margin-top: 10px; font-size: 14px; line-height: 1.3; color: var(--ink); padding-left: 0; }

  /* Back */
  .card-back { background: var(--teal); }
  .back-wordmark {
    position: absolute; left: 0; right: 0; top: 92px; text-align: center;
    font-weight: 700; font-size: 86px; line-height: 1; letter-spacing: 1px;
    color: var(--white);
  }
  .follow {
    position: absolute; left: 0; right: 0; top: 208px;
    display: flex; justify-content: center; align-items: center; gap: 10px;
    font-weight: 700; font-size: 17px; color: var(--white);
  }
  .social-mark {
    width: 28px; height: 28px; border-radius: 5px;
    background: rgba(255,255,255,0.85);
  }
  .back-web {
    position: absolute; left: 0; right: 0; top: 250px; text-align: center;
    font-size: 16px; letter-spacing: 1.5px; color: var(--white);
  }
  .back-web strong { font-weight: 700; }
</style>
</head>
<body>
<main class="stage">
  <section class="card card-front" aria-label="Card front">
    <div class="front-band"></div>
    <div class="front-wordmark">brenoloft</div>
    <div class="holder">
      <p class="holder-name">Your Name</p>
      <p class="holder-role">Position</p>
    </div>
    <ul class="contacts">
      <li>
        <svg viewBox="0 0 14 14" aria-hidden="true"><circle cx="7" cy="7" r="7" fill="#59aba7"/><path d="M4.5 3.5l1.6 0 .6 1.8-1 .8a5 5 0 0 0 2.2 2.2l.8-1 1.8.6 0 1.6c-3.5.4-6.4-2.5-6-6z" fill="#fff"/></svg>
        123-456-7890
      </li>
      <li>
        <svg viewBox="0 0 14 14" aria-hidden="true"><circle cx="7" cy="7" r="7" fill="#59aba7"/><rect x="3.5" y="4.5" width="7" height="5" fill="#fff"/><path d="M3.5 4.5l3.5 2.8 3.5-2.8" fill="none" stroke="#59aba7" stroke-width="0.9"/></svg>
        info@brenoloft.com
      </li>
      <li>
        <svg viewBox="0 0 14 14" aria-hidden="true"><circle cx="7" cy="7" r="7" fill="#59aba7"/><circle cx="7" cy="7" r="3.6" fill="none" stroke="#fff" stroke-width="1"/><path d="M3.4 7h7.2M7 3.4c-1.6 2-1.6 5.2 0 7.2M7 3.4c1.6 2 1.6 5.2 0 7.2" fill="none" stroke="#fff" stroke-width="0.8"/></svg>
        www.brenoloft.com
      </li>
      <li class="address">Street Name, City Name<br>State Zip Code</li>
    </ul>
  </section>

  <section class="card card-back" aria-label="Card back">
    <div class="back-wordmark">brenoloft</div>
    <div class="follow">
      <span>Follow Us On:</span>
      <span class="social-mark" aria-hidden="true"></span>
      <span class="social-mark" aria-hidden="true"></span>
    </div>
    <p class="back-web">www.<strong>brenoloft</strong>.com</p>
  </section>
</main>
</body>
</html>
```